New design for www.TrimTable.com

On TrimTable you can find & book your hairdresser. TrimTable is the biggest platform in the Netherlands.

- The design should be a responcive design
- Should be able to go global, should fit in perfectly between all the big booking platforms like stayvo, ridlo etc,
- Should have te result of more bookings. :)
- We are ‘only’ asking a beautiful design, not a technical solution.
- We need a homepage (https://trimtable.com/), search resultpage ((https://trimtable.com/kapper/amsterdam/#), salonpage (https://trimtable.com/kapper/vorden/lumo-for-hair/), about us page (https://trimtable.com/aboutus/), for the hairdresser info page (https://trimtable.com/kapper/), login/register page (https://trimtable.com/account/signin/).

- On the page of the hairdresser there is a dynamic part. The part where you create your appointment. Please take a look at this part too after you choose your treatment (behandeling), employee (medewerker), Date (datum) and time (tijd). The part that you see after this, is the part where you fill in your data as a consumer.

I've added more logo's but mostly we use the green color.

A few of our competitors: www.plumsalo.com, www.korifex.com

Target Market(s)

All consumers

Industry/Entity Type

Hair And Beauty

Number of Pages Required

5+ page

Font styles to use
Sans Serif

Colors
abd036
c3c3c3
757575

Requirements
Must have
• Responsive
• We did an A/B test with the homepage. It turns out that option B works better then option A (take a look at the uploaded pictures). So what we need on the homepage: The USP's with the green checkboxes, The search button needs to by dynamic (changes for example from light green to dark green so you can see you can click it) The call to action sentence Zoek & Vind je kapsalon, the searchfield and searchbutton should be seperated.
Nice to have
• The style that we like is the flat design style. The website should be simple, clean and it should feel a bit like a luxury thing. Because an appointment with the hairdresser can be a real treat and luxury moment for yourself.
• The luxury feeling and flat design that is in the www.ridlo.com website is really nice for example. But then it has to be a bit more light and not so black and dark.

```html
<!DOCTYPE html>
<html lang="en">
<head>
<meta charset="utf-8">
<title>TrimTable – Lumo for Hair</title>
<link href="https://fonts.googleapis.com/css2?family=Open+Sans:ital,wght@0,400;0,600;0,700;1,600&display=swap" rel="stylesheet">
<style>
:root{
  --green:#abd036;
  --green-dark:#8fb326;
  --green-soft:#d9ea9e;
  --footer:#9cc13a;
  --grey:#c3c3c3;
  --grey-text:#757575;
  --ink:#333;
  --panel:#efefef;
  --dark:#2a2a2a;
  --white:#fff;
}
*{box-sizing:border-box;margin:0;padding:0}
html,body{width:713px;height:1200px;overflow:hidden}
body{position:relative;font-family:"Open Sans",Arial,sans-serif;color:var(--ink);background:var(--white);font-size:10px}
.abs{position:absolute}

/* header */
.site-header{left:0;top:0;width:713px;height:70px;background:linear-gradient(100deg,#3c3f42,#5d5a55 55%,#3a3a3a)}
.brand{left:14px;top:24px;display:flex;align-items:center;gap:6px;color:var(--white);font-weight:700;font-size:15px}
.brand-mark{width:16px;height:16px;background:var(--white);border-radius:3px}
.search{left:197px;top:33px;display:flex;height:22px}
.search-field{width:190px;background:var(--white);font-size:8px;color:var(--grey-text);padding:6px 7px;white-space:nowrap}
.search-select{width:58px;background:#e6e6e6;font-size:7px;color:var(--grey-text);padding:6px 5px;border-left:1px solid var(--grey);white-space:nowrap}
.search-button{width:50px;background:var(--green);color:var(--white);font-size:8px;font-weight:600;text-align:center;padding-top:5px;margin-left:2px}
.account{left:562px;top:37px;display:flex;align-items:center;gap:6px;color:var(--white);font-size:9px}

/* salon intro */
.salon-photo{left:52px;top:114px;width:305px;height:238px;background:linear-gradient(135deg,#cfd3d6,#8d8f8c 60%,#6b5c4c)}
.salon-name{left:380px;top:114px;font-size:24px;font-weight:700;color:var(--ink);line-height:1}
.salon-name span{display:block;font-size:9px;letter-spacing:3px;color:var(--grey-text);font-weight:600;margin-top:3px}
.stars{left:572px;top:124px;display:flex;gap:2px}
.info-box{left:380px;top:184px;width:310px;height:118px;background:var(--panel);padding:10px 12px;display:flex;justify-content:space-between}
.info-box h3{font-size:9px;font-weight:700;margin-bottom:5px}
.info-box p{font-size:7.5px;color:var(--grey-text);line-height:1.55}
.hours{width:118px}
.hours h4{font-size:7.5px;color:var(--grey-text);font-weight:600;margin-bottom:4px}
.hours dl{display:grid;grid-template-columns:28px 1fr;font-size:7px;color:var(--grey-text);row-gap:2px}
.hours dt{font-weight:600}
.socials{display:flex;gap:4px;margin-top:6px}
.socials i{width:11px;height:11px;border-radius:50%;background:var(--green);display:block}
.spec-title{left:380px;top:310px;font-size:10px;font-weight:600}
.specs{left:396px;top:328px;display:flex;gap:30px}
.spec{display:flex;flex-direction:column;align-items:center;width:58px;font-size:7px;color:var(--grey-text);text-align:center;gap:3px;line-height:1.3}
.spec-icon{width:30px;height:30px;border-radius:50%;background:var(--green);display:flex;align-items:center;justify-content:center}

.page-title{left:52px;top:394px;font-size:17px;font-weight:600}
.intro{left:52px;top:422px;width:608px;font-size:8px;color:var(--grey-text);line-height:1.7}

/* booking tabs */
.booking{left:52px;top:510px;width:608px;height:370px;background:var(--white);box-shadow:0 1px 6px rgba(0,0,0,.22)}
.tabs{display:flex;height:36px;background:#f4f4f4;border-bottom:1px solid #e0e0e0}
.tab{flex:1;text-align:center;font-size:8px;font-weight:600;color:var(--grey-text);padding-top:13px;border-right:1px solid #e0e0e0}
.tab.is-active{background:var(--white);border-top:3px solid var(--green);padding-top:10px;color:var(--ink)}
.booking h2{position:absolute;left:0;width:100%;top:46px;text-align:center;color:var(--green);font-size:12px;font-weight:700}
.booking .hint{position:absolute;left:0;width:100%;top:64px;text-align:center;font-size:8px;color:var(--grey-text)}
.step{left:68px;top:118px;width:110px;height:26px;background:var(--green-soft);border:1px solid var(--green);font-size:8px;padding:7px 0 0 14px;font-weight:600}
.step svg{position:absolute;right:-12px;top:-1px}
.treatments{left:178px;top:115px;width:370px}
.row{display:flex;align-items:center;height:30px;background:var(--panel);margin-bottom:17px;font-size:8px}
.row .name{flex:1;padding-left:12px}
.row .price{width:70px}
.row .choose{width:48px;height:30px;background:var(--green);color:var(--white);text-align:center;padding-top:9px;font-weight:600}
.scroll{left:555px;top:115px;width:7px;height:220px;background:#e5e5e5}
.scroll i{display:block;height:60px;background:var(--green)}

/* newsletter */
.subscribe{left:0;top:892px;width:713px;height:108px;background:linear-gradient(180deg,#f3f3f3,#e2e2e2)}
.subscribe h2{position:absolute;top:28px;width:100%;text-align:center;font-size:13px;font-style:italic;font-weight:600;color:var(--green)}
.subscribe-form{position:absolute;left:258px;top:60px;display:flex;height:26px}
.subscribe-field{width:170px;background:var(--white);border:1px solid var(--grey);font-size:8px;font-style:italic;padding:7px 8px;color:var(--grey-text)}
.subscribe-btn{width:28px;background:var(--white);border:1px solid var(--grey);border-left:0;display:flex;align-items:center;justify-content:center}

/* footer */
.footer{left:0;top:1000px;width:713px;height:165px;background:var(--footer);color:var(--white);padding:16px 52px;display:flex;gap:28px}
.footer section{width:130px}
.footer h4{font-size:8px;font-weight:700;margin-bottom:8px;letter-spacing:.5px}
.footer p,.footer li{font-size:7px;line-height:1.7;list-style:none}
.news-form{display:flex;margin-top:4px;height:16px}
.news-form span{flex:1;background:var(--white);color:var(--grey-text);font-size:6.5px;padding:4px}
.news-form b{width:34px;background:var(--dark);font-size:6.5px;text-align:center;padding-top:4px}
.footer .socials i{background:var(--white);opacity:.85;width:13px;height:13px}
.copyright{left:0;top:1165px;width:713px;height:35px;background:var(--dark);color:#aaa;font-size:7px;text-align:center;padding-top:13px}
</style>
</head>
<body>

<header class="site-header abs" role="img" aria-label="Dimmed salon interior photograph behind the header">
</header>
<div class="brand abs"><span class="brand-mark"></span>TrimTable</div>
<div class="search abs">
  <div class="search-field">Zoek op plaats of postcode</div>
  <div class="search-select">Behandeling ▾</div>
  <div class="search-button">Search</div>
</div>
<div class="account abs">
  <svg width="10" height="10" viewBox="0 0 10 10"><circle cx="5" cy="3" r="2.2" fill="#fff"/><path d="M1 10c0-3 8-3 8 0z" fill="#fff"/></svg>
  <span>Login</span><span>|</span><span>Register</span>
</div>

<div class="salon-photo abs" role="img" aria-label="Photo of the bright salon interior with styling chairs and mirrors"></div>

<div class="salon-name abs">Lumo for Hair<span>HAIR SALON</span></div>
<div class="stars abs">
  <svg width="62" height="12" viewBox="0 0 62 12" fill="#f2b01e"><g id="st"><path d="M6 0l1.8 3.8 4.2.5-3.1 2.9.8 4.2L6 9.3 2.3 11.4l.8-4.2L0 4.3l4.2-.5z"/></g><use href="#st" x="12.5"/><use href="#st" x="25"/><use href="#st" x="37.5"/><use href="#st" x="50" fill="#c3c3c3"/></svg>
</div>

<div class="info-box abs">
  <div>
    <h3>Appointment Barber Brinkdal</h3>
    <p>Lumo for Hair<br>Lindelaan 8<br>4821 Brinkdal<br>0575-100200</p>
    <div class="socials"><i></i><i></i><i></i></div>
  </div>
  <div class="hours">
    <h4>Opening Hours</h4>
    <dl>
      <dt>Mo</dt><dd>Closed</dd>
      <dt>Tu</dt><dd>09:00 to 18:00</dd>
      <dt>We</dt><dd>09:00 to 18:00</dd>
      <dt>Th</dt><dd>09:00 to 21:00</dd>
      <dt>Fr</dt><dd>09:00 to 18:00</dd>
      <dt>Sa</dt><dd>08:00 to 16:00</dd>
    </dl>
  </div>
</div>

<div class="spec-title abs">Our specializations:</div>
<div class="specs abs">
  <div class="spec"><span class="spec-icon"><svg width="14" height="14" viewBox="0 0 14 14" fill="none" stroke="#fff" stroke-width="1.6"><circle cx="4" cy="10" r="2.5"/><circle cx="10" cy="10" r="2.5"/><path d="M5 8l6-7M9 8L3 1"/></svg></span>Extensions</div>
  <div class="spec"><span class="spec-icon"><svg width="14" height="14" viewBox="0 0 14 14" fill="#fff"><path d="M7 1l1.8 4 4.2.4-3.2 2.8 1 4.1L7 10.2 3.2 12.3l1-4.1L1 5.4l4.2-.4z"/></svg></span>Wedding hairstyles</div>
  <div class="spec"><span class="spec-icon"><svg width="14" height="14" viewBox="0 0 14 14" fill="#fff"><circle cx="7" cy="4" r="3"/><path d="M1 14c0-5 12-5 12 0z"/></svg></span>Clipper haircut</div>
</div>

<h1 class="page-title abs">Barber Lumo for Hair in Brinkdal</h1>
<p class="intro abs">Make your appointment online easily at hairdresser Lumo for Hair in Brinkdal. Day and night, simply make an appointment at the hairdresser Lumo for Hair in Brinkdal. Ladies, gentlemen and children, everyone is welcome in our salon. Browse through other salon specializations, view our price list or make an appointment. The cup of coffee with cream is ready and waiting for you!</p>

<section class="booking abs">
  <nav class="tabs">
    <div class="tab is-active">CHOOSE YOUR DATE</div>
    <div class="tab">REVIEWS</div>
    <div class="tab">TEAM</div>
    <div class="tab" style="border-right:0">PRICE LIST</div>
  </nav>
  <h2>CHOOSE YOUR DATE</h2>
  <p class="hint">Already made an appointment at TrimTable? Log in to see your previous treatment.</p>
  <div class="step abs">Treatment
    <svg width="12" height="26" viewBox="0 0 12 26"><path d="M0 0L12 13 0 26z" fill="#d9ea9e"/><path d="M0 0L12 13 0 26" fill="none" stroke="#abd036"/></svg>
  </div>
  <div class="treatments abs">
    <div class="row"><span class="name">Cute Game</span><span class="price">€ 22,75</span><span class="choose">Choose</span></div>
    <div class="row"><span class="name">Cute Game</span><span class="price">€ 22,75</span><span class="choose">Choose</span></div>
    <div class="row"><span class="name">Cute Game</span><span class="price">€ 22,75</span><span class="choose">Choose</span></div>
    <div class="row"><span class="name">Cute Game</span><span class="price">€ 22,75</span><span class="choose">Choose</span></div>
    <div class="row"><span class="name">Cute Game</span><span class="price">€ 22,75</span><span class="choose">Choose</span></div>
  </div>
  <div class="scroll abs"><i></i></div>
</section>

<section class="subscribe abs">
  <h2>Nice TrimTable get tips? Subscribe!</h2>
  <div class="subscribe-form">
    <div class="subscribe-field">Wat is je mailadres?</div>
    <div class="subscribe-btn"><svg width="10" height="10" viewBox="0 0 10 10" fill="none" stroke="#757575" stroke-width="1.5"><path d="M1 5h8M5.5 1.5L9 5 5.5 8.5"/></svg></div>
  </div>
</section>

<footer class="footer abs">
  <section>
    <h4>LINKS</h4>
    <ul><li>› Frequent Questions</li><li>› Hairdressers</li><li>› Treatments</li><li>› For Salons</li><li>› Terms of Use</li></ul>
  </section>
  <section>
    <h4>ABOUT US</h4>
    <p>TrimTable helps you find and book the right hairdresser nearby, any time of the day, in just a few simple clicks.</p>
    <p style="margin-top:6px">Salons across the country trust our platform to fill their agenda and welcome new guests every week.</p>
  </section>
  <section>
    <h4>GET IN TOUCH</h4>
    <p>Address: Lindelaan 8, 4821 Brinkdal</p>
    <p>Phone: 0575-100200</p>
    <p>Email: hello@trimtable.com</p>
  </section>
  <section>
    <h4>NEWSLETTER</h4>
    <p>Sign up for tips, offers and news from salons near you.</p>
    <div class="news-form"><span>Email address</span><b>Send</b></div>
    <div class="socials" style="margin-top:10px"><i></i><i></i><i></i></div>
  </section>
</footer>
<div class="copyright abs">Copyright © 2015. All Rights Reserved</div>

</body>
</html>
```